New B2C website design to help dads be better dads

DadHarbor is a website to help dads be the “best dad you can be.”

We require our website to be designed into a PSD format, no coding necessary.

The general concept is a two-page design. The first page is the login page, the second page is the home page. Once at the home page, rather than navigating to and from different pages, the user will push and pull through different visual and functional layers of the hierarchy. In theory, this should add to the user experience by having a visual anchor of where they are (through layered pagination) as well as improving loading times since the new information should only be a delta in data load versus a brand new page load.

The general look-and-feel we are going for is clean, simple, minimal. This means that the winning design will show us a good eye for web-optimized typography, good use of white (negative) space, and good use of a visually pleasing grid.

We require a total of 6 page "views" plus the landing page. We note that many of the views are similar to one another.
Landing page
Milestone view
Task view
Content view, articles
Content view, products
Search view
What's new view

Please review all of the additional information provided as well as the attachments for examples.

We provide the following websites as good references for:

Typography:
http://example-kelvorn.com/journal/

Use of white space:
http://www.trenvaskit.com/
http://moldrefin.com/

Example for “scrolling” page concept as well as good balance of color, typography, and white space:
http://www.qorbitalmeet.eu/

Please contact us with questions so that we can guide your design effort.
Updates

Hello designers,

The following information is added to help guide the design process:

1.  For the text dialogue below the landing page, please assume the following word count:
"why are we making dad harbor?": 250 words
"who are we?" 200 words
"what's the deal with the penguin logo?" 300 words

For the social media links, please see http://www.gravelplumbs.com/
Notice the floating "social" bar that is always to the right.  This is the concept we are going for, please try to implement this as you see fit. 

Target Market(s)

Fathers of young children ages 0-6 years old.

Industry/Entity Type

Product

Font styles to use
Sans Serif

Requirements
Must have
• Clean lines, minimal design concept

Incorporation of our logo (see attached document)

Header content is static for all views after landing page, see example

This page WILL be responsive, please keep that in mind when designing
The timeline bar should be to the left, with the timeline bar’s “milestones” also being responsive.

Designer is free to suggest font types, but any fonts used must be royalty-free and web-optimized. We request a minimum number of font types as well as fonts that load relatively fast. We reinforce that visually appealing typography is a significant factor in the winning design choice.

While we are not expecting the winning design to include code, please keep in mind that the final implementation needs to be optimized for desktop, tablet, and mobile platforms.

If you are using stock photography that is not generated by you, please provide where/how we can obtain imagery, as well as price.

All custom graphics must be available in original formats; Photoshop/GIMP layered files for layout design, and vector formats for logos, icons and other graphical elements.

Please incorporate “Blue” into design elements as you see fit, as the RGB 67 74 169 Blue is the primary color used in our brand. The complement to this blue is 255 202 0, a brownish orange. Feel free to use this color as well, although please keep it to a lesser amount.

Background color is your choice, do not feel the need to use the grey.
Should not have
• Excessive graphical content such that it affects loading times

Excessive use of too many font types such that it affects loading times

```html
<!DOCTYPE html>
<html lang="en">
<head>
<meta charset="utf-8">
<title>DadHarbor — Login</title>
<link rel="stylesheet" href="https://fonts.googleapis.com/css2?family=Open+Sans:wght@300;400&family=Source+Sans+3:wght@400;600&display=swap">
<style>
  :root {
    --brand-blue: #2f6db5;
    --logo-blue: #434aa9;
    --backdrop: #ececec;
    --page: #ffffff;
    --text-dark: #222222;
    --text-body: #444444;
    --heading-grey: #5b5b5b;
    --rule: #cfcfcf;
    --footer: #5a5a5a;
    --footer-text: #f2f2f2;
    --field-border: #a9a9a9;
  }
  * { box-sizing: border-box; margin: 0; padding: 0; }
  html, body { width: 1200px; height: 1179px; overflow: hidden; }
  body { background: var(--backdrop); font-family: "Source Sans 3", sans-serif; color: var(--text-body); position: relative; }

  .page { position: absolute; left: 181px; top: 0; width: 840px; height: 1179px; background: var(--page); }

  /* header */
  .brand { position: absolute; left: 21px; top: 76px; display: flex; align-items: center; gap: 6px; }
  .brand-mark { width: 16px; height: 16px; border-radius: 50%; background: var(--logo-blue); }
  .brand-name { font-family: "Open Sans", sans-serif; font-weight: 400; font-size: 15px; letter-spacing: 0.5px; color: var(--logo-blue); }

  .login-title { position: absolute; left: 360px; top: 32px; font-size: 12px; font-weight: 600; color: var(--brand-blue); }
  .field { position: absolute; top: 59px; width: 182px; height: 29px; border: 1px solid var(--field-border); border-radius: 3px; font-size: 10px; color: #444; padding: 8px 13px; box-shadow: inset 0 1px 2px rgba(0,0,0,.08); }
  .field--user { left: 360px; }
  .field--pass { left: 557px; }
  .btn-signin { position: absolute; left: 755px; top: 60px; width: 69px; height: 27px; border-radius: 3px; background: linear-gradient(#3d86d6, #1f62b4); color: #fff; font-size: 11px; font-weight: 600; text-align: center; line-height: 27px; }
  .help-link { position: absolute; top: 99px; font-size: 10px; font-style: italic; color: #555; }
  .help-link--forgot { left: 687px; }
  .help-link--request { left: 760px; }

  /* hero */
  .hero { position: absolute; left: 0; top: 128px; width: 840px; height: 529px; overflow: hidden;
    background: linear-gradient(100deg, #e9e9ef 0%, #e2dfe6 40%, #b89a84 62%, #8a6a55 80%, #c9b39e 100%); }
  .hero-title { position: absolute; left: 32px; top: 107px; font-family: "Open Sans", sans-serif; font-weight: 300; font-size: 33px; color: var(--brand-blue); }
  .hero-sub { position: absolute; left: 32px; top: 152px; font-family: "Open Sans", sans-serif; font-weight: 400; font-size: 19px; color: var(--text-dark); }
  .hero-copy { position: absolute; left: 34px; top: 187px; width: 380px; font-size: 11px; line-height: 21.5px; color: var(--text-dark); }
  .hero-cta { position: absolute; left: 0; width: 840px; top: 451px; text-align: center; padding-left: 0; font-family: "Open Sans", sans-serif; font-weight: 300; font-size: 26px; color: #fff; margin-left: -21px; }
  .slider-nav { position: absolute; left: 751px; top: 484px; display: flex; }
  .slider-nav span { width: 30px; height: 29px; background: rgba(140,140,140,.55); display: flex; align-items: center; justify-content: center; }
  .slider-nav span + span { margin-left: 1px; }
  .scroll-tab { position: absolute; left: 385px; top: 489px; width: 69px; height: 69px; border-radius: 50%; background: #fff; display: flex; justify-content: center; padding-top: 20px; }

  /* about */
  .about-title { position: absolute; left: 0; width: 840px; top: 692px; text-align: center; font-family: "Open Sans", sans-serif; font-weight: 300; font-size: 35px; color: var(--brand-blue); }
  .section-title { position: absolute; left: 30px; font-family: "Open Sans", sans-serif; font-weight: 300; font-size: 26px; color: var(--heading-grey); }
  .section-copy { position: absolute; left: 30px; width: 785px; font-size: 10.3px; line-height: 21.5px; color: var(--text-body); }
  .rule { position: absolute; left: 29px; top: 908px; width: 784px; height: 1px; background: var(--rule); }

  /* footer */
  .footer { position: absolute; left: 0; top: 1069px; width: 840px; height: 110px; background: var(--footer); border-top: 2px solid #8a8a8a; color: var(--footer-text); }
  .footer-nav { position: absolute; left: 32px; top: 30px; display: flex; font-size: 9.5px; }
  .footer-nav span.sep { margin: 0 16px; }
  .copyright { position: absolute; left: 32px; top: 61px; font-size: 9.5px; }
  .social { position: absolute; left: 731px; top: 39px; display: flex; gap: 7px; }
  .social span { width: 23px; height: 23px; border-radius: 50%; background: #fff; }
</style>
</head>
<body>
  <div class="page">
    <header>
      <div class="brand"><span class="brand-mark"></span><span class="brand-name">DADHARBOR</span></div>
      <div class="login-title">USER LOGIN</div>
      <div class="field field--user">User name :</div>
      <div class="field field--pass">Password :</div>
      <div class="btn-signin">Sign in</div>
      <span class="help-link help-link--forgot">Forgot login?</span>
      <span class="help-link help-link--request">Request access</span>
    </header>

    <section class="hero" role="img" aria-label="Photo of a smiling father hugging his young son outdoors">
      <h1 class="hero-title">Be the best Dad you can be</h1>
      <p class="hero-sub">The portal created exclusively for dads, by dads</p>
      <p class="hero-copy">The general concept is a two-page design. The first page is the login page, the second page is the home page. Once at the home page, rather than navigating to and from different pages, the user will push...</p>
      <div class="hero-cta">Learn about Dad Harbor</div>
      <div class="slider-nav">
        <span><svg width="10" height="16" viewBox="0 0 10 16"><path d="M8 1 L2 8 L8 15" fill="none" stroke="#fff" stroke-width="1.5"/></svg></span>
        <span><svg width="10" height="16" viewBox="0 0 10 16"><path d="M2 1 L8 8 L2 15" fill="none" stroke="#fff" stroke-width="1.5"/></svg></span>
      </div>
      <div class="scroll-tab"><svg width="20" height="12" viewBox="0 0 20 12"><path d="M2 2 L10 10 L18 2" fill="none" stroke="#666" stroke-width="3"/></svg></div>
    </section>

    <h2 class="about-title">About Dad Harbor</h2>

    <h3 class="section-title" style="top:771px">Why are we making Dad Harbor?</h3>
    <p class="section-copy" style="top:820px">Lorem ipsum dolor sit amet, consectetur adipisicing elit, sed do eiusmod tempor incididunt ut labore et dolore magna aliqua. Ut enim ad minim veniam, quis nostrud exercitation ullamco laboris nisi ut aliquip ex ea commodo consequat. Duis aute irure dolor in reprehenderit in voluptate velit esse cillum dolore eu fugiat nulla pariatur. Excepteur sint occaecat cupidatat non proident, sunt in culpa qui officia deserunt mollit anim id est laborum</p>

    <div class="rule"></div>

    <h3 class="section-title" style="top:922px">Who are we?</h3>
    <p class="section-copy" style="top:972px">Lorem ipsum dolor sit amet, consectetur adipisicing elit, sed do eiusmod tempor incididunt ut labore et dolore magna aliqua. Ut enim ad minim veniam, quis nostrud exercitation ullamco laboris nisi ut aliquip ex ea commodo consequat. Duis aute irure dolor in reprehenderit in voluptate velit esse cillum dolore eu fugiat nulla pariatur. Excepteur sint occaecat cupidatat non proident, sunt in culpa qui officia deserunt mollit anim id est laborum</p>

    <footer class="footer">
      <nav class="footer-nav">
        <span>Home</span><span class="sep">|</span>
        <span>About</span><span class="sep">|</span>
        <span>Prepare for the baby arrival</span><span class="sep">|</span>
        <span>What's the latest?</span><span class="sep">|</span>
        <span>Car Seats</span>
      </nav>
      <div class="copyright">Copyright 2013. Dad Harbor. All rights reserved.</div>
      <div class="social"><span></span><span></span><span></span></div>
    </footer>
  </div>
</body>
</html>
```